Flyer für Veranstaltungstechnik-Unternehmen
Zielgruppe
VERANSTALTUNGSTECHNIK
Aufgabenstellung
Wir haben diesen Flyer erhalten, finden ihn aber nicht ansprechend, sehr altmodisch und möchten einen klar strukturierten modernen Flyer.
DIN A5 „Heft“ – Und das Profil als „Einleger“. Sollte dementsprechend ca. 1 cm umlaufend kleiner sein.
Der Flyer soll sich an dem Design der Webseite orientieren!

```html
<!DOCTYPE html>
<html lang="de">
<head>
<meta charset="utf-8">
<title>Flyer Veranstaltungstechnik – Profil und Über uns</title>
<link href="https://fonts.googleapis.com/css2?family=Montserrat:wght@800&family=Source+Sans+3:wght@300;400;600;700&display=swap" rel="stylesheet">
<style>
  :root {
    --backdrop: #a6a6a6;
    --paper: #ffffff;
    --ink-dark: #1b1b1b;
    --accent: #9c82c4;
    --text: #f2f2f2;
    --text-soft: #dcdcdc;
  }
  * { margin: 0; padding: 0; box-sizing: border-box; }
  html, body {
    width: 1200px; height: 852px; overflow: hidden;
    background: var(--backdrop);
    font-family: "Source Sans 3", sans-serif;
    color: var(--text);
  }
  .spread { position: relative; width: 1200px; height: 852px; }
  .page {
    position: absolute; top: 64px; width: 515px; height: 725px;
    background: var(--paper); padding: 7px;
  }
  .page--profile { left: 86px; }
  .page--about { left: 616px; }
  .page__inner {
    position: relative; width: 100%; height: 100%; overflow: hidden;
    background: var(--ink-dark);
  }
  .stage-glow {
    position: absolute; left: 0; right: 0; bottom: 0; height: 260px;
    background:
      radial-gradient(ellipse 40% 45% at 30% 80%, rgba(160,160,160,0.45), transparent 70%),
      radial-gradient(ellipse 30% 35% at 65% 70%, rgba(120,120,120,0.35), transparent 70%),
      linear-gradient(to bottom, transparent, #2a2a2a 60%, #141414);
  }
  .portrait {
    position: absolute; left: 28px; top: 82px; width: 198px; height: 241px;
    background: linear-gradient(160deg, #d6d6d6 0%, #b8b8b8 45%, #6e6e6e 100%);
  }
  .person { position: absolute; left: 258px; top: 82px; width: 230px; }
  .person__name {
    font-family: "Montserrat", sans-serif; font-weight: 800;
    font-size: 23px; line-height: 28px; color: var(--accent);
    text-transform: uppercase;
  }
  .person__role { margin-top: 24px; font-size: 12.5px; line-height: 16px; font-weight: 600; }
  .person__role span { display: block; }
  .person__qualification { margin-top: 12px; font-size: 12px; line-height: 14.5px; font-weight: 400; }
  .person__address { margin-top: 11px; font-size: 12px; line-height: 14.5px; font-weight: 400; padding-left: 1px; }
  .person__contact { margin-top: 14px; list-style: none; font-size: 12px; font-weight: 400; }
  .person__contact li { display: flex; align-items: center; gap: 6px; height: 17px; }
  .person__contact svg { width: 12px; height: 12px; flex: none; }
  .profile-text { position: absolute; left: 28px; top: 363px; width: 456px; }
  .profile-text__lead { font-size: 13.6px; line-height: 17px; font-weight: 700; }
  .profile-text p {
    margin-top: 14px; font-size: 12.2px; line-height: 14.35px; font-weight: 400;
    text-align: justify; color: var(--text-soft);
  }
  .event-photo {
    position: absolute; inset: 0;
    background:
      radial-gradient(ellipse 45% 30% at 70% 28%, #9a9a9a, transparent 75%),
      linear-gradient(to bottom, #202020 0%, #5a5a5a 30%, #3a3a3a 48%, #1a1a1a 70%, #070707 100%);
  }
  .about { position: absolute; left: 21px; top: 322px; width: 460px; }
  .about__title {
    font-family: "Montserrat", sans-serif; font-weight: 800;
    font-size: 21px; letter-spacing: 0.42em; color: var(--accent);
    margin-left: 7px; text-transform: uppercase; word-spacing: -0.4em;
  }
  .about p {
    margin-top: 14px; font-size: 12.2px; line-height: 14.35px; font-weight: 400;
    text-align: justify; color: var(--text);
  }
  .about p:first-of-type { margin-top: 10px; }
</style>
</head>
<body>
<main class="spread">
  <section class="page page--profile">
    <div class="page__inner">
      <div class="stage-glow" role="img" aria-label="Bühnenlicht mit Scheinwerfern im Nebel"></div>
      <div class="portrait" role="img" aria-label="Porträtfoto der Projektleiterin"></div>
      <div class="person">
        <h1 class="person__name">Carla<br>Wendt</h1>
        <p class="person__role"><span>TECHNISCHE LEITUNG</span><span>Produktions &amp; Projektleitung</span></p>
        <p class="person__qualification">Fachkraft für Veranstaltungstechnik<br>und Veranstaltungskauffrau</p>
        <p class="person__address">Lindenhofweg 14<br>12459 Berlin</p>
        <ul class="person__contact">
          <li>
            <svg viewBox="0 0 12 12" aria-hidden="true"><circle cx="6" cy="6" r="6" fill="var(--accent)"/><path d="M4 3.2c.4-.3.7-.2.9.2l.5 1c.1.3 0 .5-.2.7l-.3.3c.3.7.9 1.3 1.6 1.6l.3-.3c.2-.2.4-.3.7-.2l1 .5c.4.2.5.5.2.9-.5.6-1.2.8-2 .4C5.3 7.6 4.4 6.7 3.7 5.3c-.4-.8-.2-1.5.3-2.1z" fill="#fff"/></svg>
            +49 170 5550 1234
          </li>
          <li>
            <svg viewBox="0 0 12 12" aria-hidden="true"><circle cx="6" cy="6" r="6" fill="var(--accent)"/><rect x="3" y="4" width="6" height="4.2" rx=".5" fill="none" stroke="#fff" stroke-width=".8"/><path d="M3.2 4.3 6 6.4l2.8-2.1" fill="none" stroke="#fff" stroke-width=".8"/></svg>
            wendt@lumenwerk-berlin.de
          </li>
        </ul>
      </div>
      <div class="profile-text">
        <h2 class="profile-text__lead">Technische Leitung für die Planung, Organisation und Durchführung der Veranstaltungen vor Ort sowie die technische Planung und Koordination.</h2>
        <p>Seit Frühjahr 2020 bin ich als Projekt- und Produktionsleiterin Teil des Event-Teams der Lumenwerk Events GmbH.</p>
        <p>Mit meinen Ausbildungen zur Veranstaltungskauffrau und Veranstaltungstechnikerin bin ich seit 2010 in der Eventbranche tätig und betrachte Projekte aus beiden Perspektiven, um ein breites Portfolio an Veranstaltungen planen, umsetzen und betreuen zu können. Durch meine langjährige Berufserfahrung in der Branche, auch im Bereich Dekorationsbau, konnte ich mir ein breites Spektrum an Kompetenzen und Erfahrungen aneignen, unter anderem in den Bereichen Veranstaltungssicherheit, Behördenkommunikation und Begleitung von Genehmigungsverfahren, Sicherheitskonzepte, Dienstleisterauswahl, Tourneeplanung oder Prüfung von Dienstleister- und Locationverträgen. Ebenso stehe ich Kunden bei der Beratung, Prüfung und Umsetzung aller Aspekte zur Seite. Ich unterstütze Kunden nicht nur bei der Vorplanung und Budgetierung, sondern auch im On-Site-Management und in der Nachbereitung der Veranstaltung.</p>
      </div>
    </div>
  </section>

  <section class="page page--about">
    <div class="page__inner">
      <div class="event-photo" role="img" aria-label="Konferenzsaal mit Publikum, Bühne, Rednerpult und Kamera"></div>
      <div class="about">
        <h2 class="about__title">Über uns</h2>
        <p>Gemeinsam mit Ihnen und nach Ihren Wünschen setzen wir Veranstaltungskonzepte und Ideen um. Wir sorgen für einen reibungslosen Ablauf. 1996 startete die Lumenwerk GmbH als Dienstleister für Film und Fernsehen. Seitdem sorgen wir mit unserer Firmenphilosophie, unseren nachhaltig durchdachten Konzepten und unseren rund 40 Mitarbeiter:innen für Flexibilität, Vertrauen und Transparenz in der Umsetzung Ihrer Projekte.</p>
        <p>Durch unsere Zusammenarbeit mit renommierten Medienhäusern wie Kanal Nord, Studio West, Radio Elbe und Tele Havel haben wir Fachkompetenzen im Bereich der TV-Produktionen und Übertragungen von Veranstaltungen.</p>
        <p>Wir bieten flexible Komplettlösungen für Veranstaltungen aller Art und realisieren große Events mit einem Rundum-Service, der mehrere Bereiche des Eventmanagements gleichzeitig abdeckt. Denn neben der Planung und Durchführung bieten wir auch einen umfangreichen Technikverleih und das passende Fachpersonal für Ihre Veranstaltung.</p>
        <p>Unser Event-Team zeichnet sich durch fachliches Know-how aus unterschiedlichen Ausbildungsrichtungen aus und betrachtet Ihre Veranstaltung sowohl aus kaufmännischer als auch aus technischer Sicht mit einem unterstützenden Faktor aus dem Managementbereich.</p>
      </div>
    </div>
  </section>
</main>
</body>
</html>
```